Recipe Card Design

I have a small kitchen store in Livingston Montana, and I would like to have recipe cards (4x6 postcard) designed with my logo, lines for recipe writing, all in black and white. My website is here: www.brambleforkcookware.com

Store

```html
<!DOCTYPE html>
<html lang="en">
<head>
<meta charset="utf-8">
<title>Bramble Fork Cookware – Recipe Card</title>
<link rel="stylesheet" href="https://fonts.googleapis.com/css2?family=Alfa+Slab+One&family=Oswald:wght@700&family=Poppins:wght@400&display=swap">
<style>
  :root {
    --ink: #000000;
    --paper: #ffffff;
    --rule: 3.6px;
  }
  html, body {
    margin: 0;
    padding: 0;
    overflow: hidden;
    background: var(--paper);
  }
  .card {
    position: relative;
    width: 1200px;
    height: 929px;
    background: var(--paper);
    color: var(--ink);
    overflow: hidden;
  }
  .brand {
    position: absolute;
    left: 84px;
    top: 50px;
    width: 370px;
    height: 456px;
    display: flex;
    flex-direction: column;
    justify-content: center;
    align-items: center;
    text-align: center;
    font-family: "Oswald", sans-serif;
    font-weight: 700;
    color: var(--ink);
    text-transform: uppercase;
    line-height: 1.02;
  }
  .brand__word { display: block; }
  .brand__word--lead { font-size: 86px; letter-spacing: 2px; }
  .brand__word--mid { font-size: 86px; letter-spacing: 2px; }
  .brand__word--tail { font-size: 58px; letter-spacing: 4px; }

  .label {
    position: absolute;
    margin: 0;
    color: var(--ink);
    text-transform: uppercase;
    line-height: 1;
  }
  .label--title {
    left: 498px;
    top: 64px;
    font-family: "Alfa Slab One", serif;
    font-size: 50px;
    letter-spacing: 0.5px;
  }
  .label--section {
    font-family: "Oswald", sans-serif;
    font-weight: 700;
    font-size: 29px;
    letter-spacing: 0.3px;
  }
  .label--ingredients { left: 504px; top: 202px; }
  .label--instructions { left: 518px; top: 477px; }

  .rule {
    position: absolute;
    height: var(--rule);
    background: var(--ink);
  }
  .rule--short { left: 714px; width: 402px; }
  .rule--mid { left: 508px; width: 608px; }
  .rule--full { left: 86px; width: 1030px; }

  .site {
    position: absolute;
    right: 36px;
    top: 878px;
    margin: 0;
    font-family: "Poppins", sans-serif;
    font-size: 17px;
    color: var(--ink);
  }
</style>
</head>
<body>
<main class="card">
  <div class="brand" aria-label="Bramble Fork Cookware">
    <span class="brand__word brand__word--lead">Bramble</span>
    <span class="brand__word brand__word--mid">Fork</span>
    <span class="brand__word brand__word--tail">Cookware</span>
  </div>

  <h1 class="label label--title">Recipe</h1>
  <div class="rule rule--short" style="top:108px"></div>
  <div class="rule rule--mid" style="top:164px; left:510px; width:606px"></div>

  <h2 class="label label--section label--ingredients">Ingredients</h2>
  <div class="rule rule--short" style="top:224px"></div>
  <div class="rule rule--mid" style="top:276px; left:504px; width:612px"></div>
  <div class="rule rule--mid" style="top:332px; left:504px; width:612px"></div>
  <div class="rule rule--mid" style="top:388px"></div>
  <div class="rule rule--mid" style="top:443px"></div>

  <h2 class="label label--section label--instructions">Instructions</h2>
  <div class="rule rule--short" style="top:500px; left:708px; width:408px"></div>

  <div class="rule rule--full" style="top:556px"></div>
  <div class="rule rule--full" style="top:612px"></div>
  <div class="rule rule--full" style="top:668px"></div>
  <div class="rule rule--full" style="top:724px"></div>
  <div class="rule rule--full" style="top:780px"></div>
  <div class="rule rule--full" style="top:836px"></div>

  <p class="site">www.brambleforkcookware.com</p>
</main>
</body>
</html>
```